Verodex business card

Business card for sustainable investment company called "Verodex". Verodex is an exchange platform selling carbon credits between buyers and sellers. Carbon Credits are an environmental commodity for reducing global carbon emissions.

the card should obviously have our logo and the theme should be sustainability/environment mixed with a trading platform.

Contact Information for Business Card

Logo, Name, Title, Phone, Email

Colors
0054AA
0677BA
7BADD7
CADEEF
E8F1F8
0094D4
00A9DD
6FCCEA
C7EBF8
E9F6FB
00AB8E
00BBA5
67D7C9
C6EFE9
E9F9F6
59FF00
82FF00
B8FF75
E3FFCB
F4FFEA

```html
<!DOCTYPE html>
<html lang="en">
<head>
<meta charset="UTF-8">
<title>Verodex business card</title>
<link href="https://fonts.googleapis.com/css2?family=Montserrat:wght@400;500;700&display=swap" rel="stylesheet">
<style>
  :root {
    --navy: #14295a;
    --sky: #29abe2;
    --sky-light: #6fccea;
    --blue: #0054aa;
    --ink: #1b1f2a;
    --paper: #ffffff;
    --stage: #e6e8ec;
  }
  * { box-sizing: border-box; margin: 0; padding: 0; }
  html, body { width: 1200px; height: 900px; overflow: hidden; }
  body {
    background: var(--stage);
    font-family: "Montserrat", sans-serif;
    position: relative;
  }
  .card {
    position: absolute;
    width: 600px;
    height: 343px;
    box-shadow: 0 10px 28px rgba(0,0,0,0.25);
    overflow: hidden;
  }
  .card--back { left: 90px; top: 80px; background: var(--navy); }
  .card--front { left: 510px; top: 470px; background: var(--paper); }

  .wordmark {
    display: flex;
    align-items: center;
    gap: 18px;
  }
  .wordmark__dot {
    width: 46px; height: 46px;
    border-radius: 50%;
    background: var(--sky);
    flex: none;
  }
  .wordmark__name {
    font-weight: 700;
    font-size: 54px;
    letter-spacing: 2px;
    line-height: 1;
  }
  .card--back .wordmark {
    position: absolute;
    left: 0; right: 0; top: 50%;
    transform: translateY(-50%);
    justify-content: center;
  }
  .card--back .wordmark__name { color: var(--paper); }

  .card--front .wordmark {
    position: absolute;
    left: 150px; top: 52px;
  }
  .card--front .wordmark__dot { width: 40px; height: 40px; }
  .card--front .wordmark__name { color: var(--navy); font-size: 48px; }

  .identity {
    position: absolute;
    left: 110px; top: 128px;
    width: 200px;
    text-align: right;
  }
  .identity__name {
    font-weight: 700;
    font-size: 22px;
    letter-spacing: 0.5px;
    white-space: nowrap;
  }
  .identity__first { color: var(--sky); }
  .identity__last { color: var(--navy); }
  .identity__title {
    font-size: 14px;
    color: var(--ink);
    margin-top: 4px;
  }
  .divider {
    position: absolute;
    left: 326px; top: 122px;
    width: 1.5px; height: 70px;
    background: var(--sky);
  }
  .contacts {
    position: absolute;
    left: 342px; top: 120px;
    list-style: none;
    display: flex; flex-direction: column; gap: 6px;
  }
  .contacts__item {
    display: flex; align-items: center; gap: 8px;
    font-size: 13.5px; color: var(--ink);
    white-space: nowrap;
  }
  .contacts__icon { width: 14px; height: 14px; flex: none; }
  .wave { position: absolute; left: 0; bottom: 0; width: 600px; height: 343px; }
</style>
</head>
<body>
  <section class="card card--back" aria-label="Card back">
    <div class="wordmark">
      <span class="wordmark__dot"></span>
      <span class="wordmark__name">VERODEX</span>
    </div>
  </section>

  <section class="card card--front" aria-label="Card front">
    <svg class="wave" viewBox="0 0 600 343" aria-hidden="true">
      <defs>
        <linearGradient id="swoosh" x1="0" y1="0" x2="1" y2="0">
          <stop offset="0" stop-color="#6fccea"/>
          <stop offset="0.55" stop-color="#29abe2"/>
          <stop offset="1" stop-color="#0054aa"/>
        </linearGradient>
      </defs>
      <path d="M95 343 C260 330 380 305 430 260 C480 215 520 180 600 168 L600 343 Z" fill="#14295a"/>
      <path d="M60 312 C220 305 350 292 410 248 C375 298 250 322 85 332 Z" fill="url(#swoosh)"/>
    </svg>

    <div class="wordmark">
      <span class="wordmark__dot"></span>
      <span class="wordmark__name">VERODEX</span>
    </div>

    <div class="identity">
      <p class="identity__name"><span class="identity__first">DANIEL</span> <span class="identity__last">MARSH</span></p>
      <p class="identity__title">Co-Founder</p>
    </div>

    <div class="divider"></div>

    <ul class="contacts">
      <li class="contacts__item">
        <svg class="contacts__icon" viewBox="0 0 16 16"><path d="M3 2 L6 2 L7 5 L5 6.5 C6 8.5 7.5 10 9.5 11 L11 9 L14 10 L14 13 C14 14 13 14.5 12 14.3 C7 13.5 2.5 9 1.7 4 C1.5 3 2 2 3 2 Z" fill="#29abe2"/></svg>
        <span>555-210-4836</span>
      </li>
      <li class="contacts__item">
        <svg class="contacts__icon" viewBox="0 0 16 16"><rect x="1" y="3" width="14" height="10" rx="1" fill="#29abe2"/><path d="M1.5 3.5 L8 9 L14.5 3.5" fill="none" stroke="#fff" stroke-width="1.3"/></svg>
        <span>info@verodex.com</span>
      </li>
      <li class="contacts__item">
        <svg class="contacts__icon" viewBox="0 0 16 16"><circle cx="8" cy="8" r="7" fill="#29abe2"/><path d="M1 8 H15 M8 1 C5 4 5 12 8 15 M8 1 C11 4 11 12 8 15" fill="none" stroke="#fff" stroke-width="1"/></svg>
        <span>www.verodex.com</span>
      </li>
    </ul>
  </section>
</body>
</html>
```